Marigold Synchronized Swim Team's Clubhouse (web page)

Fun, Super Easy to read and navigate. Please error on the side of too large font sizes rather than too small font sizes.

We are a New Orleans (USA) based club for adults and youth of all genders.

We have youth and adult performance and competition teams. We teach synchronized swimming. We perform at special events.

Webpage should allow for

1. Sign up for classes, camps and teams (pay fees, sign waivers, reserve a spot and link to national Delmar Aquaform club membership website in order to buy required national membership).Make our multi step registration process easy, quick, pleasant.

2. Provide an area to upload practice schedules.
and performance calendar.

3. Easily
Hire one of our synchro squad to perform at special events.

4. Embedded Google Calndar

5 Members only site
( one away for youth and one area for adults. )

6 Show off our new logo, photos and videos. Be able to change these images often.

Our team colors are red, aqua and pink.

7. Buy logo gear

Click to team shop at
Brindle cove.com and other future team shops.

8. One click to become a sponsor of the team.

An area to show off sponsor logos. We will have several levels of sponsorships. It is important to have small medium and large logo spots. WE also will have a wall of names of folks who donate 10 - 100 dollars to sponsor the team.

We want the experience to be fun . We do not want headache producing events.

Our team colors are red, pink and aqua. WE have not settled on a specific red or pink yet. You are free to play around with different tones and hues. I tend toward a sholcking pink and cherry red. But really do want to see what your thoughts are for our reds and pinks. Also feel free to vary aqua from a light to dark. But we do want to stay away from navy.
Thanks for your hard work and creativity.

Target Market(s)

All ages, genders and ethnicity. Swimmers, dancers and event planners.

Coding

Coded - Design and coding required

Number of Pages Required

4 page

Font styles to use
Sans Serif

Colors
ec1f27
0293ce
f59195

Requirements
Must have
• See p descriptions +
• Fine #20 is our logo and
• Playful, bold, elegant, Colorful (red, aqua and pink are our team colors).
• I want to be able to plug in / update photos , schedules, release forms, almost everything as our seasons change. I do not know ( Newbury) do I want coded or incised site. All advice welcome.
Nice to have
• Your flare as a designer. Thank you for making us better through your creativity, ability to edit, clarify and advice. :-)
Should not have
• Confusion.

```html
<!DOCTYPE html>
<html lang="en">
<head>
<meta charset="utf-8">
<title>Marigold Synchronized Swim Team – Clubhouse</title>
<link href="https://fonts.googleapis.com/css2?family=Open+Sans:wght@400;600;700;800&display=swap" rel="stylesheet">
<style>
:root{
  --red:#ec1f27;
  --aqua:#0293ce;
  --pink:#f59195;
  --ink:#404040;
  --body:#555555;
  --rule:#e2e2e2;
  --footer:#ececec;
  --cal-green:#2e9e86;
  --white:#ffffff;
}
*{box-sizing:border-box;margin:0;padding:0}
html,body{width:1200px;height:2528px;overflow:hidden;background:var(--white)}
body{position:relative;font-family:"Open Sans",Arial,sans-serif;color:var(--ink)}
a{text-decoration:none}

/* header + hero */
.hero{position:absolute;left:0;top:0;width:1200px;height:661px}
.hero-photo{position:absolute;inset:0;
  background:
    radial-gradient(ellipse 420px 260px at 180px 420px,rgba(74,92,196,.55),transparent 70%),
    radial-gradient(ellipse 420px 260px at 1020px 430px,rgba(74,92,196,.55),transparent 70%),
    radial-gradient(ellipse 500px 200px at 600px 600px,rgba(220,240,248,.45),transparent 70%),
    linear-gradient(180deg,#5cc6dc 0%,#2ea9c9 45%,#168bb3 100%)}
.hero-shade{position:absolute;inset:0;background:radial-gradient(ellipse 520px 200px at 600px 400px,rgba(0,40,70,.28),transparent 75%)}
.hero-top{position:absolute;left:0;top:0;width:1200px;height:175px}
.brand{position:absolute;left:76px;top:58px;display:flex;align-items:center;gap:10px}
.brand-dot{width:26px;height:26px;border-radius:50%;background:var(--aqua)}
.brand-name{font-weight:800;font-size:26px;color:var(--aqua);letter-spacing:.5px}
.brand-tag{position:absolute;left:76px;top:96px;font-size:11px;color:var(--aqua);font-weight:600}
.nav{position:absolute;top:42px;right:74px;display:flex;gap:16px}
.btn{display:inline-flex;align-items:center;justify-content:center;border-radius:30px;
  font-weight:700;text-transform:uppercase;font-size:15px;height:40px}
.btn-outline-aqua{border:2px solid var(--aqua);color:var(--aqua);background:var(--white)}
.btn-red{background:var(--red);color:var(--white)}
.nav .upload{width:268px}
.nav .calendar{width:240px}
.nav .signup{width:152px;gap:8px}
.hero-copy{position:absolute;left:0;top:305px;width:1200px;text-align:center;color:var(--white);text-shadow:0 2px 6px rgba(0,0,0,.25)}
.hero-title{font-size:58px;font-weight:800;line-height:1.1}
.hero-sub{font-size:29px;font-weight:700;line-height:40px;margin-top:6px}
.hero-cta{position:absolute;left:473px;top:483px;width:255px;height:48px;font-size:17px}

/* sections */
.section-title{position:absolute;left:0;width:1200px;text-align:center;font-size:70px;font-weight:600;color:var(--ink)}
.rule{position:absolute;left:76px;width:1048px;height:2px;background:var(--rule)}

.event{position:absolute;top:814px;width:330px}
.event-photo{width:330px;height:214px}
.event-title{margin-top:18px;font-size:24px;font-weight:700;color:var(--aqua);line-height:31px;text-transform:uppercase}
.event-text{margin-top:8px;font-size:15px;line-height:25px;color:var(--body)}
.read-more{margin-top:9px;font-size:13px;font-weight:700;color:var(--red);text-transform:uppercase;display:flex;align-items:center;gap:6px}
.btn-view{position:absolute;left:465px;top:1272px;width:270px;height:52px;border:2px solid var(--pink);color:var(--ink);font-weight:600;font-size:17px;background:var(--white)}

/* calendar */
.cal{position:absolute;left:300px;top:1528px;width:600px;height:393px;border:3px solid #e4e4e4;background:var(--white)}
.cal-month{position:absolute;left:0;top:8px;width:100%;text-align:center;font-family:Arial,Helvetica,sans-serif;font-size:46px;color:var(--cal-green)}
.cal-head{position:absolute;left:14px;top:95px;width:564px;display:grid;grid-template-columns:repeat(7,1fr);font-family:Arial,sans-serif;font-size:9px}
.cal-head span{padding-left:24px}
.cal-head .we{color:var(--red)}
.cal-grid{position:absolute;left:14px;top:107px;width:564px;display:grid;grid-template-columns:repeat(7,1fr);grid-auto-rows:47px;border-top:1.5px solid #333}
.cal-grid div{position:relative;border-right:1.5px solid #333;border-bottom:1.5px solid #333;font-family:Arial,sans-serif;font-size:25px;text-align:right;padding-right:6px;color:#111}
.cal-grid div:nth-child(7n){border-right:none}
.cal-grid .out{color:#b5b5b5}
.cal-grid .we{color:var(--red)}
.cal-grid .end{border-bottom:none}
.cal-grid small{position:absolute;left:6px;bottom:3px;font-size:6px;color:#333;white-space:nowrap}
.cal-grid .hol small{color:var(--red)}

/* tiles */
.tile{position:absolute;top:2010px;width:511px;height:277px;color:var(--white);text-align:center}
.tile-photo{position:absolute;inset:0}
.tile-copy{position:absolute;left:0;width:100%;text-shadow:0 2px 6px rgba(0,0,0,.3)}
.tile-title{font-size:54px;font-weight:700;line-height:50px}
.tile-btns{display:flex;gap:14px;justify-content:center;margin-top:26px;text-shadow:none}
.btn-aqua{background:var(--aqua);color:var(--white);width:138px;height:42px;font-size:16px}
.btn-pink{background:var(--pink);color:var(--white);width:138px;height:42px;font-size:16px}

/* footer */
.footer{position:absolute;left:0;top:2334px;width:1200px;height:194px}
.footer-brand{position:absolute;left:76px;top:2440px;display:flex;align-items:center;gap:6px}
.footer-brand .brand-dot{width:14px;height:14px}
.footer-brand .brand-name{font-size:15px}
.copyright{position:absolute;left:199px;top:2428px;font-size:13px;font-weight:600;line-height:20px;color:var(--ink)}
.social{position:absolute;left:960px;top:2448px;display:flex;gap:14px}
.social span{width:22px;height:22px;border-radius:4px;background:#8a8a8a}
</style>
</head>
<body>

<section class="hero">
  <div class="hero-photo" role="img" aria-label="Photo of synchronized swimmers in blue suits raising their arms in the pool"></div>
  <div class="hero-shade"></div>
  <svg class="hero-top" viewBox="0 0 1200 175" preserveAspectRatio="none" aria-hidden="true">
    <defs><linearGradient id="sky" x1="0" y1="0" x2="0" y2="1"><stop offset="0" stop-color="#ffffff"/><stop offset="1" stop-color="#eaf6fb"/></linearGradient></defs>
    <path d="M0 0H1200V110C900 160 600 100 300 150 180 170 80 160 0 140Z" fill="url(#sky)"/>
    <path d="M0 140C80 160 180 170 300 150 600 100 900 160 1200 110" fill="none" stroke="#ec1f27" stroke-width="5"/>
  </svg>
  <div class="brand"><span class="brand-dot"></span><span class="brand-name">MARIGOLD</span></div>
  <div class="brand-tag">NOLA Synchronized Swim Team</div>
  <nav class="nav">
    <a class="btn btn-outline-aqua upload">Upload Practice Schedules</a>
    <a class="btn btn-outline-aqua calendar">Performance Calendar</a>
    <a class="btn btn-red signup">
      <svg width="13" height="14" viewBox="0 0 13 14"><circle cx="6.5" cy="4" r="3.5" fill="#fff"/><path d="M0 14C0 9 3 8 6.5 8S13 9 13 14Z" fill="#fff"/></svg>
      Sign Up</a>
  </nav>
  <div class="hero-copy">
    <h1 class="hero-title">MARIGOLD SWIM CLUB</h1>
    <p class="hero-sub">We are a New Orleans (USA) based club for<br>adults and youth of all genders.</p>
  </div>
  <a class="btn btn-red hero-cta">Become a Member</a>
</section>

<h2 class="section-title" style="top:695px">Special Events</h2>

<article class="event" style="left:76px">
  <div class="event-photo" role="img" aria-label="Photo of a plush octopus and toy fish on a towel" style="background:radial-gradient(ellipse 120px 80px at 250px 70px,rgba(200,40,30,.6),transparent 70%),radial-gradient(ellipse 90px 60px at 90px 40px,rgba(230,90,40,.55),transparent 70%),linear-gradient(135deg,#e9aa55,#d88a3c)"></div>
  <h3 class="event-title">Duis aliquam nibh a dui iaculis viverra</h3>
  <p class="event-text">Aenean a nibh eget turpis vehicula tempus ac sed massa. Vestibulum dolor nulla, ultrices ac tincidunt sed, laoreet non est.</p>
  <a class="read-more">Read More <svg width="12" height="12" viewBox="0 0 12 12"><circle cx="6" cy="6" r="5" fill="none" stroke="#ec1f27" stroke-width="1.6"/><path d="M4 5l2 2 2-2" fill="none" stroke="#ec1f27" stroke-width="1.6"/></svg></a>
</article>
<article class="event" style="left:435px">
  <div class="event-photo" role="img" aria-label="Photo of swimmers performing a leg display at a pool edge with spectators" style="background:linear-gradient(180deg,#7d8088 0%,#9aa2a8 30%,#49b6d6 55%,#2aaed2 100%)"></div>
  <h3 class="event-title">Duis aliquam nibh a dui iaculis viverra</h3>
  <p class="event-text">Aenean a nibh eget turpis vehicula tempus ac sed massa. Vestibulum dolor nulla, ultrices ac tincidunt sed, laoreet non est.</p>
  <a class="read-more">Read More <svg width="12" height="12" viewBox="0 0 12 12"><circle cx="6" cy="6" r="5" fill="none" stroke="#ec1f27" stroke-width="1.6"/><path d="M4 5l2 2 2-2" fill="none" stroke="#ec1f27" stroke-width="1.6"/></svg></a>
</article>
<article class="event" style="left:794px">
  <div class="event-photo" role="img" aria-label="Photo of swimmers splashing in a turquoise pool" style="background:radial-gradient(ellipse 90px 60px at 165px 80px,rgba(240,250,252,.75),transparent 70%),linear-gradient(135deg,#30c4dc,#1596bd)"></div>
  <h3 class="event-title">Duis aliquam nibh a dui iaculis viverra</h3>
  <p class="event-text">Aenean a nibh eget turpis vehicula tempus ac sed massa. Vestibulum dolor nulla, ultrices ac tincidunt sed, laoreet non est.</p>
  <a class="read-more">Read More <svg width="12" height="12" viewBox="0 0 12 12"><circle cx="6" cy="6" r="5" fill="none" stroke="#ec1f27" stroke-width="1.6"/><path d="M4 5l2 2 2-2" fill="none" stroke="#ec1f27" stroke-width="1.6"/></svg></a>
</article>

<a class="btn btn-view">View All Events</a>
<div class="rule" style="top:1376px"></div>

<h2 class="section-title" style="top:1413px">Club Calendar</h2>

<div class="cal">
  <div class="cal-month">December 2016</div>
  <div class="cal-head"><span>Monday</span><span>Tuesday</span><span>Wednesday</span><span>Thursday</span><span>Friday</span><span class="we">Saturday</span><span class="we">Sunday</span></div>
  <div class="cal-grid">
    <div class="out">28</div><div class="out">29</div><div class="out">30</div><div>1</div><div>2</div><div class="we">3</div><div class="we">4</div>
    <div>5</div><div>6</div><div>7</div><div>8</div><div>9</div><div class="we">10</div><div class="we">11</div>
    <div>12</div><div>13</div><div>14</div><div>15</div><div>16</div><div class="we">17</div><div class="we">18</div>
    <div>19</div><div>20</div><div>21</div><div>22</div><div>23</div><div class="we">24<small>Christmas Eve</small></div><div class="we hol">25<small>Christmas Day</small></div>
    <div class="we hol">26<small>Christmas Day (observed)</small></div><div>27</div><div>28</div><div>29</div><div>30</div><div class="we">31<small>New Year's Eve</small></div><div class="out">1</div>
    <div class="out end">2</div><div class="out end">3</div><div class="out end">4</div><div class="out end">5</div><div class="out end">6</div><div class="out end">7</div><div class="out end">8</div>
  </div>
</div>

<div class="rule" style="top:1967px"></div>

<section class="tile" style="left:76px">
  <div class="tile-photo" role="img" aria-label="Photo of swimmers in red caps and goggles" style="background:radial-gradient(ellipse 160px 90px at 120px 60px,rgba(200,50,60,.7),transparent 70%),radial-gradient(ellipse 160px 90px at 420px 60px,rgba(200,50,60,.6),transparent 70%),linear-gradient(135deg,#8c3b40,#4e4248)"></div>
  <div class="tile-copy" style="top:55px">
    <h2 class="tile-title">Members<br>Only Site</h2>
    <div class="tile-btns"><a class="btn btn-aqua">Youth</a><a class="btn btn-aqua">Adults</a></div>
  </div>
</section>
<section class="tile" style="left:615px">
  <div class="tile-photo" role="img" aria-label="Photo of team gear printed with the club artwork" style="background:radial-gradient(ellipse 260px 140px at 260px 170px,rgba(170,170,170,.5),transparent 70%),linear-gradient(135deg,#7e7e7e,#5a5a5a)"></div>
  <div class="tile-copy" style="top:92px">
    <h2 class="tile-title">Team Shop</h2>
    <div class="tile-btns"><a class="btn btn-pink">Shop Now</a></div>
  </div>
</section>

<footer>
  <svg class="footer" viewBox="0 0 1200 194" preserveAspectRatio="none" aria-hidden="true">
    <path d="M0 20C300 60 700 -10 1200 30V194H0Z" fill="#ececec"/>
    <path d="M0 20C300 60 700 -10 1200 30" fill="none" stroke="#0293ce" stroke-width="4"/>
  </svg>
  <div class="footer-brand"><span class="brand-dot"></span><span class="brand-name">MARIGOLD</span></div>
  <p class="copyright">Copyright © 2016. Company Name.<br>All Right Reserved</p>
  <div class="social"><span></span><span></span><span></span><span></span><span></span></div>
</footer>

</body>
</html>
```